2-Page Flyer for the Information Session about the Quiet Pathfinder Course

This is a flyer to announce/advertise an evening Information Session about the Quiet Pathfinder Course. This Program aims at mindfully rethinking and redesigning work (and life) for people who feel stuck or not entirely satisfied with their work and/or life (please see draft flyer attached for more details). This Program is property of Bright Meadow, a company that uses a combination of Mindfulness, Design, and Entrepreneurship to help people achieve greater happiness (in their work and lives).

Target Market(s)

People who feel stuck or not entirely satisfied with their work and/or life (please see draft flyer attached for more details)

Font styles to use
Serif
Sans Serif

Colors
ffffff
f37122
33a6d7
acd037

Requirements
Must have
• All of what I will say below is suggestive (I’m not a design expert), and I’m open to divert from it, if it makes sense and feels more interesting.
• I thought initially of a 2-page flyer (please see draft flyer attached). The first page could help people grasp the essence of the event quickly (in 1 or 2 minutes), and then, if they are interested/motivated, they would continue reading through page 2, which has more info about the Program in itself.
• Potential Structure
• Page 1
• . About the Information Session on the Quiet Pathfinder Course
• . Visible Date & Time, Contacts, Venue (and other relevant info)
• . About me (the facilitator)
• Page 2
• . About the Quiet Pathfinder Course
• I include a Powerpoint draft of the flyer with the content. The design is rudimentary and precarious from an aesthetics/organization point of view, and this is mainly where I need help (and maybe in other aspects too!).
• On the flyer, I would like to include:
• . A photo of myself (I attach 1 picture).
• . 1 or 2 beautiful-nature photos (cropped or full). One may have to do with looking at the sky, dreaming, and imagining a new work and life (2 photos with sky and clouds attached). The other has to do with walking the transformation journey (the photo with the person walking through the forest path).
• . bright meadow logo or logos (there are two slightly different ones, that can be used for different purposes). For the first page, I would like the bright meadow logo that has "bright meadow" written on the bottom, with the saying "Stillness, Craft and Venture for Bright Meadow" beneath. This is the main logo. For the 2nd page, you can choose the logo that adapts better.
• - Where it says the "the way out is in" it would be great to have a similar font to the one I attach (see file "Font_the_way_out_is_in.png" and Ankecallig-fg.ttf
Nice to have
• In terms of colours, I would not divert much from the logo colours (and of course white and black). I would like the flyer to be quite white. Almost like fairy-tale white: the white horse, the white snow, the white of the stars, the white heaven. White could be the base colour. White means peace, tranquillity, calm contentment, a smile.
• And then use the other colours. The green of the mindfulness. The blue of the sky, the dreams. And the orange of the sun, the energy, the fire, the action. And maybe the black for text.
• Where it says the "the way out is in" it would be great to have a similar font to the one I attach (see file "Font_the_way_out_is_in".
• I would like this flyer to be a piece of art, in every possible way. Simple, beautiful, ease, light, peaceful, calm happy. Just like the Quiet Pathfinder Course and bright meadow Company that I am creating intends to be. The mission of this Program and Company is to be a designer, a painter (a Picasso) of happier and more fulfilling human lives.
• I am very much looking forward to seeing your proposal(s).

```html
<!DOCTYPE html>
<html lang="en">
<head>
<meta charset="utf-8">
<title>Quiet Pathfinder Course – Information Session Flyer</title>
<link href="https://fonts.googleapis.com/css2?family=Roboto:ital,wght@0,300;0,400;0,500;0,700;0,900;1,400;1,500&family=Roboto+Condensed:wght@700&family=Dancing+Script:wght@700&display=swap" rel="stylesheet">
<style>
:root{
  --white:#ffffff;
  --orange:#f37122;
  --orange-band:#e8843a;
  --blue:#33a6d7;
  --green:#acd037;
  --grey:#9a9a9a;
  --ink:#1b1b1b;
  --text:#2a2a2a;
  --backdrop:#f4f4f6;
}
*{margin:0;padding:0;box-sizing:border-box}
html,body{width:1200px;height:1200px;overflow:hidden}
body{background:var(--backdrop);font-family:'Roboto',sans-serif;color:var(--text);position:relative}
.page{position:absolute;top:256px;width:478px;height:675px;background:var(--white);overflow:hidden;box-shadow:0 6px 18px rgba(0,0,0,.12)}
.page--front{left:93px}
.page--back{left:646px}
.abs{position:absolute}

/* front page */
.sky-photo{left:0;top:0;width:478px;height:306px;background:linear-gradient(180deg,#7fb2e0 0%,#b9d4ec 30%,#cfdfe8 48%,#8aa6a8 62%,#6f8f6a 80%,#7d9460 100%)}
.orange-rule{left:0;top:306px;width:478px;height:6px;background:var(--orange-band)}
.brand{left:0;width:478px;text-align:center}
.brand__mark{top:28px;left:219px;width:40px;height:40px;border-radius:50%;background:var(--orange)}
.brand__name{top:92px;font-size:24px;font-weight:300;color:var(--blue);letter-spacing:-.3px}
.brand__tag{top:122px;font-size:8.5px;font-style:italic;color:#222}
.title{left:0;top:156px;width:478px;text-align:center;font-family:'Roboto Condensed',sans-serif;font-weight:700;font-size:28px;line-height:26px;color:var(--ink)}
.session-tag{left:95px;top:221px;width:289px;height:22px;border:1.5px solid var(--white);background:var(--orange);color:var(--white);font-family:'Roboto Condensed',sans-serif;font-weight:700;font-size:16px;letter-spacing:2.2px;text-align:center;line-height:19px}
.when{left:0;top:248px;width:478px;text-align:center;font-family:'Roboto Condensed',sans-serif;font-weight:700;font-size:17px;line-height:17px;color:var(--ink)}
.venue{left:0;top:288px;width:478px;text-align:center;font-size:10.5px;color:var(--ink)}
.venue b{font-weight:700}
.copy{font-size:8.2px;line-height:11.2px;color:var(--text)}
.intro{left:36px;top:321px;width:410px}
.section-title{font-size:11px;font-weight:500;color:var(--blue)}
.who{left:36px;top:355px;width:410px}
.who p{margin-top:1px}
.facilitator-line{left:152px;top:440px;font-size:7.5px;color:var(--ink)}
.facilitator-line .label{color:#8aa82b}
.facilitator-line .name{font-size:11px;font-weight:500;margin:0 3px}
.facilitator-line i{font-size:6.8px;font-weight:500}
.bio-box{left:31px;top:455px;width:419px;height:129px;background:var(--blue)}
.portrait{left:31px;top:406px;width:112px;height:178px;background:linear-gradient(180deg,#c7c2bd 0%,#8f8881 35%,#3f4650 70%,#2f3842 100%)}
.bio{left:153px;top:459px;width:289px;font-size:7.6px;line-height:10.9px;color:var(--ink);text-align:justify}
.link-bar{left:98px;top:583px;width:282px;height:17px;background:var(--orange);color:var(--white);font-size:8.8px;line-height:17px;text-align:center}
.link-bar i{font-weight:500}
.booking{left:0;top:617px;width:478px;text-align:center;font-size:11.5px;font-weight:500;color:var(--ink)}
.contact{font-size:10px;color:var(--ink);display:flex;align-items:center;gap:4px}
.contact svg{width:8px;height:8px;flex:none}
.contact--mail{left:106px;top:636px}
.contact--phone{left:274px;top:636px}
.contact-note{left:286px;top:650px;font-size:6px;font-style:italic;color:var(--ink)}
.bottom-band{left:0;top:661px;width:478px;height:14px;background:var(--orange-band)}

/* back page */
.header-band{left:0;top:24px;width:475px;height:65px;background:linear-gradient(100deg,#0d3f9e 0%,#1a5fc2 55%,#3f8de0 100%)}
.header-band h2{position:absolute;left:29px;top:6px;font-size:13px;font-weight:500;color:var(--white)}
.header-band p{position:absolute;left:29px;top:26px;width:422px;font-size:7px;line-height:9.6px;color:#e8f0fb;text-align:justify}
.journey{left:22px;top:110px;width:264px;height:170px}
.journey text{font-family:'Roboto',sans-serif}
.program{left:293px;top:117px;width:155px}
.program h3,.why h3,.how h3{font-size:12.5px;font-weight:500;margin-bottom:4px}
.program h3,.how h3{color:var(--blue)}
.why h3{color:var(--orange)}
.program p{font-size:7.2px;line-height:10.4px;text-align:justify;color:var(--ink);margin-bottom:9px}
.why{left:30px;top:292px;width:192px}
.how{left:247px;top:292px;width:205px}
.why p,.how p{font-size:7.2px;line-height:10.4px;color:var(--ink)}
.why p.lead{text-align:justify}
.points{list-style:none;margin-top:10px}
.points li{font-size:7.2px;line-height:10.4px;color:var(--ink);padding-left:10px;position:relative}
.points li::before{content:attr(data-n);position:absolute;left:0;top:2px;width:7px;height:7px;border-radius:50%;font-size:5px;line-height:7px;text-align:center;color:var(--white);font-weight:700}
.points--orange li::before{background:var(--orange)}
.points--green li::before{background:#7fb82b}
.how p.format{margin-top:12px}
.forest-photo{left:0;top:458px;width:475px;height:177px;background:linear-gradient(90deg,#2b2414 0%,#4a4020 30%,#6a6433 50%,#3f3a1c 70%,#231d10 100%)}
.quote{left:124px;top:590px;width:230px;text-align:center;font-family:'Dancing Script',cursive;font-weight:700;font-size:24px;color:var(--white)}
.mini-brand{left:370px;top:600px;display:flex;align-items:center;gap:5px}
.mini-brand span.dot{width:16px;height:16px;border-radius:50%;background:var(--orange)}
.mini-brand span.word{font-size:10px;line-height:10px;font-weight:300;color:var(--orange)}
.footer-band{left:0;top:635px;width:475px;height:39px;background:var(--blue)}
.footer-item{top:11px;font-size:9px;color:var(--ink);display:flex;align-items:center;gap:3px}
.footer-item svg{width:7px;height:7px}
.footer-item--phone{left:41px}
.footer-item--web{left:184px}
.footer-item--mail{left:338px}
.footer-note{left:36px;top:23px;font-size:7px;font-style:italic;color:#1d3b4d}
</style>
</head>
<body>

<section class="page page--front">
  <div class="abs sky-photo" role="img" aria-label="Photo of wide mountain valley under a bright sky with soft white clouds"></div>
  <div class="abs orange-rule"></div>

  <div class="abs brand__mark"></div>
  <div class="abs brand brand__name">bright meadow</div>
  <div class="abs brand brand__tag">Stillness, Craft and Venture for Bright Meadow</div>

  <h1 class="abs title">QUIET PATHFINDER<br>COURSE</h1>
  <div class="abs session-tag">FREE INFORMATION SESSION</div>
  <div class="abs when">THURSDAY 5TH SEPTEMBER 2019<br>19:30 TO 21:00</div>
  <div class="abs venue"><b>Venue:</b> Nalu Coworking, C/ Olivera 12, Barcelona</div>

  <div class="abs bottom-band"></div>

  <p class="abs copy intro">The purpose of this free <b>Information Session</b> is to give you a real insight into the <b>Quiet Pathfinder Course</b> and how it can help you make the most of your professional and personal life.</p>

  <div class="abs who">
    <h3 class="section-title">WHO CAN COME</h3>
    <p class="copy">Whether you come on your own, or with friends or family, you'll be warmly welcomed. The session will take place on Thursday the 5th September 2019, from 19:30 to 21:00, at NALU Coworking. Please see information below to get in contact or to book a seat.</p>
  </div>

  <div class="abs facilitator-line"><span class="label">Facilitator:</span><span class="name">DR TOMAS VARELA</span><i>Visiting Research Fellow, Northmoor University</i></div>
  <div class="abs bio-box"></div>
  <div class="abs portrait" role="img" aria-label="Portrait photo of the facilitator in a dark jacket and scarf"></div>
  <p class="abs bio">Tomas joined the Northmoor University School of Management as a Lecturer in Entrepreneurship in 2015. He completed his PhD in Entrepreneurship at Kelvin Business School in 2014, receiving the prestigious Society of Management Studies' Ardent Doctoral Dissertation Award. He began his business career as a Production Engineer for Voltrix, and later as a Sales Engineer for Halden Works. After his MBA, he served as a Strategy Consultant for Douro Business School. Originally from Portugal, Tomas enjoys designing and launching new ideas, international communities, mindfulness retreats, and musical improvisation. He nurtures a close connection to Lotus Valley Mindfulness Centre, where he has practiced and volunteered over 9 months. He has a broad experience of sharing the benefits of mindfulness with others.</p>
  <div class="abs link-bar">More about the facilitator: <i>www.brightmeadow.io/team/tvarela</i></div>

  <div class="abs booking">INFORMATION &amp; BOOKING</div>
  <div class="abs contact contact--mail">
    <svg viewBox="0 0 10 10"><rect x="0.5" y="2" width="9" height="6.5" rx="1" fill="none" stroke="#f37122" stroke-width="1.2"/><path d="M1 2.5 5 6 9 2.5" fill="none" stroke="#f37122" stroke-width="1.2"/></svg>
    hello@brightmeadow.io
  </div>
  <div class="abs contact contact--phone">
    <svg viewBox="0 0 10 10"><path d="M2 1 3.8 3 3 4.2Q4.2 6.4 5.8 7L7 6.2 9 8 8 9.3Q4.5 9.5 1.2 5 0.5 2.5 2 1Z" fill="#f37122"/></svg>
    +34 611 402 735
  </div>
  <div class="abs contact-note">(Video call and messaging)</div>
</section>

<section class="page page--back">
  <div class="abs header-band">
    <h2>What is Quiet Pathfinding</h2>
    <p>Being mindful means being aware and awake. Entrepreneurship is the creation of a new form of organising. Quiet Pathfinding is then the process of creating or redesigning your work and life with awareness, in a way that is reflective of you, of your passions and values, thus conducing to a greater sense of fulfilment and happiness.</p>
  </div>

  <svg class="abs journey" viewBox="0 0 264 170" role="img" aria-label="Four monthly workshops in sequence, supported by weekly peer support meetings">
    <g font-size="7" text-anchor="middle" fill="#fff">
      <rect x="0" y="30" width="54" height="54" rx="6" fill="#acd037"/>
      <text x="27" y="50">Workshop 1</text><text x="27" y="59">INSIGHT</text><text x="27" y="70" font-style="italic">5 hours</text>
      <rect x="70" y="30" width="54" height="54" rx="6" fill="#33a6d7"/>
      <text x="97" y="50">Workshop 2</text><text x="97" y="59">DESIGN</text><text x="97" y="70" font-style="italic">3 hours</text>
      <rect x="140" y="30" width="54" height="54" rx="6" fill="#f37122"/>
      <text x="167" y="50">Workshop 3</text><text x="167" y="59">EXECUTE</text><text x="167" y="70" font-style="italic">5 hours</text>
      <rect x="210" y="30" width="54" height="54" rx="6" fill="#9a9a9a"/>
      <text x="237" y="50">Workshop 4</text><text x="237" y="59">PRESENT</text><text x="237" y="70" font-style="italic">5 hours</text>
    </g>
    <g fill="none" stroke="#555" stroke-width="1.5">
      <path d="M57 57h9M62 53l4 4-4 4"/>
      <path d="M127 57h9M132 53l4 4-4 4"/>
      <path d="M197 57h9M202 53l4 4-4 4"/>
    </g>
    <g font-size="7.5" fill="#1b1b1b" text-anchor="middle">
      <text x="132" y="14">One workshop each month · 4 months</text>
    </g>
    <rect x="0" y="104" width="264" height="30" rx="15" fill="none" stroke="#d6d6d6" stroke-width="1.2"/>
    <g font-size="7.5" fill="#1b1b1b" text-anchor="middle">
      <text x="132" y="117">Weekly Peer Support (WPS) meetings</text>
      <text x="132" y="127">(2 hours/week) between every workshop</text>
    </g>
  </svg>

  <div class="abs program">
    <h3>The Program</h3>
    <p>The <b>Quiet Pathfinder Course</b> is a <b>4-month long transformative</b> journey designed for people who feel stuck or not entirely satisfied with their professional and/or personal life. It will be of benefit for everyone, at any stage.</p>
    <p>The Program entails a five-hour workshop each month, complemented by two-hour weekly peer support meetings. It combines mindfulness techniques, design thinking methodology,</p>
  </div>

  <div class="abs why">
    <h3>Why</h3>
    <p class="lead">Many people are not satisfied with their work, but they don't know what to do about it. This Program offers you a safe place to conduct your inner journey with collective support, helping you reflect, design, and (very likely) do something about it. It aims at:</p>
    <ul class="points points--orange">
      <li data-n="1">Increasing awareness, clarity and confidence</li>
      <li data-n="2">Having a deeper <b><i>insight</i></b> on what makes you happier and what you want</li>
      <li data-n="3">Developing a clear <b><i>design</i></b> integrating your intended work and life</li>
      <li data-n="4">Start <b><i>executing</i></b> this design.</li>
    </ul>
  </div>

  <div class="abs how">
    <h3>How</h3>
    <p>This Program differs from existing entrepreneurial programs in many ways:</p>
    <ul class="points points--green">
      <li data-n="1">Uses mindfulness and self analysis to look deeply into yourself</li>
      <li data-n="2">Design and execution decisions are based on happiness rather than (only) financials</li>
      <li data-n="3">Holistic and inclusive design process, integrating work and life, and building synergies</li>
    </ul>
    <p class="format">Format includes: lectures, individual work, group sharing, guided activities, experiential exercises, video, audio, handouts and other resources.</p>
  </div>

  <div class="abs forest-photo" role="img" aria-label="Photo of a person walking down a long path through a dark pine forest"></div>
  <div class="abs quote">“The Way Out is In”</div>
  <div class="abs mini-brand"><span class="dot"></span><span class="word">bright<br>meadow</span></div>

  <div class="abs footer-band">
    <div class="abs footer-item footer-item--phone">
      <svg viewBox="0 0 10 10"><path d="M2 1 3.8 3 3 4.2Q4.2 6.4 5.8 7L7 6.2 9 8 8 9.3Q4.5 9.5 1.2 5 0.5 2.5 2 1Z" fill="#1b1b1b"/></svg>+34 611 402 735
    </div>
    <div class="abs footer-note">(Video call and messaging)</div>
    <div class="abs footer-item footer-item--web">
      <svg viewBox="0 0 10 10"><circle cx="5" cy="5" r="4.2" fill="none" stroke="#1b1b1b"/><path d="M1 5h8M5 1c-2 2.5-2 5.5 0 8M5 1c2 2.5 2 5.5 0 8" fill="none" stroke="#1b1b1b" stroke-width=".8"/></svg>www.brightmeadow.io
    </div>
    <div class="abs footer-item footer-item--mail">
      <svg viewBox="0 0 10 10"><rect x="0.5" y="2" width="9" height="6.5" rx="1" fill="none" stroke="#1b1b1b" stroke-width="1.2"/><path d="M1 2.5 5 6 9 2.5" fill="none" stroke="#1b1b1b" stroke-width="1.2"/></svg>hello@brightmeadow.io
    </div>
  </div>
</section>

</body>
</html>
```